Tallon Electrical Business Card

We need a business card design for our family-run electrical contracting business based in Western Australia called 'Tallon Electrical'. We provide electrical services including residential, commercial and industrial. We aim for individual business cards to be made for all of our employees. We already have a company logo, which we require to be featured on the design. We would like simple, sleek and vibrant designs, which incorporate our logo and represent our business. We do not want anything involving too many graphics/images. We like the colours red, black, white and all shades of grey. The final design should communicate professionalism and trustworthiness.
We require the following contact information:
Name- Grant Pellow
EC 5871
Mobile number- 0455 870 219
Fax number (including area code)- (08) 9560 2831
Email adress- name@tallonelectrical.com.au
Electrical
- ITC Handel Bold

```html
<!DOCTYPE html>
<html lang="en">
<head>
<meta charset="utf-8">
<title>Tallon Electrical Business Card</title>
<link rel="stylesheet" href="https://fonts.googleapis.com/css2?family=Arimo:wght@400;700&display=swap">
<style>
  :root {
    --red: #e02027;
    --red-deep: #b5141a;
    --black: #1c1c1c;
    --charcoal: #2b2b2b;
    --grey-text: #4a4a4a;
    --white: #ffffff;
    --paper: #f4f4f4;
    --stage: #3a3a3a;
  }
  * { box-sizing: border-box; margin: 0; padding: 0; }
  html, body { width: 1200px; height: 900px; overflow: hidden; }
  body {
    background: var(--stage);
    font-family: "Arimo", Arial, sans-serif;
    display: flex;
    align-items: center;
    justify-content: center;
    gap: 40px;
  }
  .card {
    position: relative;
    width: 520px;
    height: 318px;
    overflow: hidden;
    box-shadow: 0 10px 30px rgba(0,0,0,0.45);
  }

  /* Front */
  .card-front { background: linear-gradient(180deg, var(--white), var(--paper)); }
  .card-front .swoosh { position: absolute; left: 0; bottom: 0; width: 100%; height: 150px; }
  .brand {
    position: absolute;
    display: flex;
    align-items: center;
    gap: 10px;
    font-weight: 700;
    text-transform: uppercase;
    letter-spacing: 1px;
    white-space: nowrap;
  }
  .brand-mark { width: 18px; height: 18px; }
  .card-front .brand { left: 30px; top: 62px; font-size: 25px; color: var(--black); }
  .card-front .brand-mark { background: var(--red); }

  .contact {
    position: absolute;
    right: 22px;
    top: 44px;
    text-align: right;
    color: var(--grey-text);
    font-size: 13px;
    line-height: 1.3;
  }
  .contact-row { display: flex; justify-content: flex-end; align-items: flex-start; gap: 12px; }
  .contact-row .icon { width: 12px; height: 12px; flex: none; margin-top: 2px; }
  .contact-name { color: var(--red); font-weight: 700; font-size: 14px; }
  .contact-role { margin-right: 24px; margin-bottom: 16px; }
  .contact-block { margin-bottom: 2px; }
  .contact-email {
    position: absolute;
    right: 46px;
    top: 190px;
    font-size: 13px;
    color: var(--grey-text);
  }

  /* Back */
  .card-back { background: linear-gradient(160deg, var(--red) 40%, var(--red-deep)); }
  .card-back .brand { left: 50%; top: 118px; transform: translateX(-50%); font-size: 30px; color: var(--white); }
  .card-back .brand-mark { background: var(--white); }
  .service-band {
    position: absolute;
    left: 0; right: 0;
    bottom: 46px;
    height: 24px;
    background: var(--charcoal);
    color: var(--white);
    font-size: 12px;
    font-weight: 700;
    letter-spacing: 0.5px;
    display: flex;
    align-items: center;
    justify-content: center;
    gap: 6px;
  }
  .service-band .divider { color: #888; font-weight: 400; }
</style>
</head>
<body>

  <section class="card card-front" aria-label="Business card front">
    <svg class="swoosh" viewBox="0 0 520 150" preserveAspectRatio="none" aria-hidden="true">
      <path d="M0,28 C120,95 330,80 520,40 L520,150 L0,150 Z" fill="var(--red)"/>
      <path d="M0,10 C130,62 330,68 520,30 C330,58 150,52 0,28 Z" fill="var(--black)"/>
      <path d="M0,28 C120,95 330,80 520,40 L520,48 C330,88 120,100 0,38 Z" fill="var(--white)"/>
    </svg>

    <div class="brand"><span class="brand-mark"></span>Tallon Electrical</div>

    <div class="contact">
      <div class="contact-row"><span class="contact-name">Grant Pellow</span>
        <svg class="icon" viewBox="0 0 12 12" aria-hidden="true"><path d="M6 0a4 4 0 0 1 4 4c0 3-4 8-4 8S2 7 2 4a4 4 0 0 1 4-4zm0 2.5a1.5 1.5 0 1 0 0 3 1.5 1.5 0 0 0 0-3z" fill="var(--red)"/></svg>
      </div>
      <div class="contact-role">Director</div>
      <div class="contact-row contact-block"><span>EC 5871, address<br>town here 6542U</span>
        <svg class="icon" viewBox="0 0 12 12" aria-hidden="true" style="margin-top:18px"><rect x="1.5" y="1.5" width="9" height="9" rx="1" fill="none" stroke="var(--red)" stroke-width="1.5"/></svg>
      </div>
      <div class="contact-row"><span>0455 870 219</span>
        <svg class="icon" viewBox="0 0 12 12" aria-hidden="true"><rect x="3" y="1" width="6" height="3" fill="var(--red)"/><rect x="1" y="4.5" width="10" height="4.5" rx="1" fill="var(--red)"/><rect x="3" y="8" width="6" height="3" fill="var(--red)"/></svg>
      </div>
      <div class="contact-row"><span>(08) 9560 2831</span>
        <svg class="icon" viewBox="0 0 12 12" aria-hidden="true"><rect x="1" y="2.5" width="10" height="7" fill="var(--red)"/><path d="M1 2.5l5 4 5-4" fill="none" stroke="var(--white)" stroke-width="1"/></svg>
      </div>
    </div>
    <div class="contact-email">name@tallonelectrical.com.au</div>
  </section>

  <section class="card card-back" aria-label="Business card back">
    <div class="brand"><span class="brand-mark"></span>Tallon Electrical</div>
    <div class="service-band">
      <span>Residential</span><span class="divider">|</span>
      <span>Industrial</span><span class="divider">|</span>
      <span>Commercial</span>
    </div>
  </section>

</body>
</html>
```